Wellbrook Talking Therapies Hub Swindon

We need a design for magazine advert, ideally high resolution to advertise our counselling centre. we would like this to include a photo of two people talking, as if in a counselling session. See our logo and colour range on our website. www.wbtth-swindon.co.uk
The photo should not include cups of coffee, clipboards, desks, people touching. it needs to be two people in armchairs sympathetically listening and looking at each other.
The font type is Great Vibes on the logo. Our design should communicate a centre of excellence delivering high quality, professional services in stylishly furnished surroundings.

Hello Everyone We have had a number of designs that look quite promising but are missing the brief. Can I reiterate that we need a photograph of 2 people seated talking to each other in a sincere way. There shouldn't be office chairs but comfortable chairs. There should be no physical contact. There should be no clipboards.Thank you very muchHeather Added Sunday, March 12, 2017

Target Market(s)

people seeking counselling and psychotherapy

Font styles to use
Other font styles liked:
• Great Vibes as in our logo for some of the print. See attached file.

Requirements
Must have
• good photograph
• Two high res Pixavend photos:
• https://pixavend-files.example-cdn.net/download?id=a81kd93jf02mdl47xq
• https://pixavend-files.example-cdn.net/download?id=z57pw20ne84bvc13ty
Nice to have
• Watermark in keeping with our logo.
Should not have
• Darkness

```html
<!DOCTYPE html>
<html lang="en">
<head>
<meta charset="utf-8">
<title>Wellbrook Talking Therapies Hub – Magazine Advert</title>
<link rel="stylesheet" href="https://fonts.googleapis.com/css2?family=Great+Vibes&family=Montserrat:wght@400;500;700&family=Open+Sans:ital,wght@1,400&display=swap">
<style>
  :root {
    --paper: #ffffff;
    --cream: #ece5d3;
    --sage: #86a572;
    --sage-dark: #6f8e5d;
    --sage-light: #a3bf8c;
    --brown: #3b2f2c;
    --brown-light: #574845;
    --ink: #2e2523;
    --icon: #6f6663;
    --white: #ffffff;
  }
  html, body {
    margin: 0;
    padding: 0;
    width: 1106px;
    height: 1200px;
    overflow: hidden;
    background: var(--paper);
  }
  .advert {
    position: relative;
    width: 1106px;
    height: 1200px;
    overflow: hidden;
    background: var(--paper);
    font-family: "Montserrat", sans-serif;
    color: var(--ink);
  }
  .advert-shapes {
    position: absolute;
    inset: 0;
  }
  .headline {
    position: absolute;
    top: 28px;
    right: 60px;
    margin: 0;
    font-family: "Great Vibes", cursive;
    font-weight: 400;
    font-size: 56px;
    line-height: 1.05;
    color: var(--ink);
    text-align: left;
  }
  .headline .line-two { display: block; }
  .quote {
    position: absolute;
    top: 150px;
    left: 70px;
    width: 370px;
    margin: 0;
    font-family: "Open Sans", sans-serif;
    font-style: italic;
    font-size: 17px;
    line-height: 1.45;
    color: var(--white);
  }
  .quote cite {
    display: block;
    text-align: right;
    font-style: italic;
    margin-top: 4px;
  }
  .team {
    position: absolute;
    left: 50px;
    top: 838px;
    width: 420px;
    color: var(--white);
  }
  .team-intro {
    margin: 0 0 14px;
    font-family: "Great Vibes", cursive;
    font-size: 62px;
    line-height: 1;
    font-weight: 400;
  }
  .team-highlight {
    margin: 0 0 8px;
    font-weight: 700;
    font-size: 23px;
    line-height: 1.3;
    color: var(--sage-light);
  }
  .team-detail {
    margin: 0;
    font-size: 21px;
    line-height: 1.35;
    font-weight: 500;
  }
  .brand {
    position: absolute;
    left: 560px;
    top: 838px;
    width: 520px;
    display: flex;
    align-items: center;
    gap: 14px;
  }
  .brand-dot {
    width: 22px;
    height: 22px;
    border-radius: 50%;
    background: var(--sage);
    flex: none;
  }
  .brand-name {
    font-family: "Great Vibes", cursive;
    font-size: 36px;
    color: var(--ink);
    line-height: 1.1;
    white-space: nowrap;
  }
  .contact {
    position: absolute;
    left: 560px;
    top: 910px;
    width: 500px;
  }
  .contact-hours {
    margin: 0 0 16px;
    font-size: 22px;
    font-weight: 500;
    line-height: 1.3;
  }
  .contact-list {
    list-style: none;
    margin: 0;
    padding: 0;
  }
  .contact-item {
    display: flex;
    align-items: center;
    gap: 16px;
    margin-bottom: 10px;
  }
  .contact-icon { width: 28px; height: 28px; flex: none; }
  .contact-phone { font-size: 40px; font-weight: 500; letter-spacing: 1px; }
  .contact-address { font-size: 20px; line-height: 1.3; }
  .contact-web { font-size: 21px; }
</style>
</head>
<body>
<main class="advert">
  <svg class="advert-shapes" width="1106" height="1200" viewBox="0 0 1106 1200">
    <defs>
      <linearGradient id="quoteFill" x1="0" y1="0" x2="1" y2="0">
        <stop offset="0" stop-color="#7b9a69"/>
        <stop offset="1" stop-color="#8dab79"/>
      </linearGradient>
      <linearGradient id="brownFill" x1="0" y1="0" x2="0" y2="1">
        <stop offset="0" stop-color="#574845"/>
        <stop offset="1" stop-color="#2e2321"/>
      </linearGradient>
      <linearGradient id="photoFill" x1="0" y1="0" x2="1" y2="1">
        <stop offset="0" stop-color="#e9ecea"/>
        <stop offset="0.45" stop-color="#cfe3dc"/>
        <stop offset="1" stop-color="#e8d3c8"/>
      </linearGradient>
    </defs>
    <path class="cream-field" d="M0 640 C 320 600, 720 520, 1106 410 L1106 1200 L0 1200 Z" fill="var(--cream)"/>
    <rect class="quote-panel" x="40" y="115" width="420" height="230" rx="26" fill="url(#quoteFill)"/>
    <rect class="team-panel" x="0" y="720" width="500" height="480" fill="url(#brownFill)"/>
    <path class="photo-frame" role="img" aria-label="Photograph of two women seated on a sofa in a bright, softly furnished counselling room, smiling"
      d="M40 790 C 70 520, 320 360, 640 360 C 840 360, 990 410, 1070 450 C 1000 660, 800 800, 520 805 C 320 808, 160 800, 40 790 Z"
      fill="url(#photoFill)" stroke="var(--sage)" stroke-width="10"/>
  </svg>

  <h1 class="headline">Confidential Therapeutic Services<span class="line-two">in the Heart of Old Town</span></h1>

  <blockquote class="quote">
    “A big part of letting go is recognising when it is time to stay in a situation and when it is time to move on.”
    <cite>- Edwin R. Marlow</cite>
  </blockquote>

  <section class="team">
    <p class="team-intro">We have over</p>
    <p class="team-highlight">30 carefully selected, qualified and professional therapists</p>
    <p class="team-detail">offering a range of services to help individuals, families and couples.</p>
  </section>

  <div class="brand">
    <span class="brand-dot"></span>
    <span class="brand-name">Wellbrook Talking Therapies Hub</span>
  </div>

  <section class="contact">
    <p class="contact-hours">Appointments available<br>throughout the day and evening</p>
    <ul class="contact-list">
      <li class="contact-item">
        <svg class="contact-icon" viewBox="0 0 24 24" aria-hidden="true"><path d="M6.6 10.8c1.4 2.8 3.8 5.1 6.6 6.6l2.2-2.2c.3-.3.7-.4 1-.2 1.1.4 2.3.6 3.6.6.6 0 1 .4 1 1V20c0 .6-.4 1-1 1C10.6 21 3 13.4 3 4c0-.6.4-1 1-1h3.5c.6 0 1 .4 1 1 0 1.3.2 2.5.6 3.6.1.3 0 .7-.2 1z" fill="none" stroke="var(--icon)" stroke-width="1.6"/></svg>
        <span class="contact-phone">01632 960418</span>
      </li>
      <li class="contact-item">
        <svg class="contact-icon" viewBox="0 0 24 24" aria-hidden="true"><path d="M12 2a7 7 0 0 0-7 7c0 5.2 7 13 7 13s7-7.8 7-13a7 7 0 0 0-7-7z" fill="none" stroke="var(--icon)" stroke-width="1.6"/><circle cx="12" cy="9" r="2.5" fill="none" stroke="var(--icon)" stroke-width="1.6"/></svg>
        <span class="contact-address">14 Elmcroft Lane, Old Town,<br>Swindon SN1 9ZX</span>
      </li>
      <li class="contact-item">
        <svg class="contact-icon" viewBox="0 0 24 24" aria-hidden="true"><circle cx="12" cy="12" r="9" fill="none" stroke="var(--icon)" stroke-width="1.6"/><path d="M3 12h18M12 3c3 3 3 15 0 18M12 3c-3 3-3 15 0 18" fill="none" stroke="var(--icon)" stroke-width="1.4"/></svg>
        <span class="contact-web">www.wbtth-swindon.co.uk</span>
      </li>
    </ul>
  </section>
</main>
</body>
</html>
```